New Business card design to reflect rebrand

I would like a business card design with a good base colour for our new logo and also a placeholder for a profile pic of the card holder. the design needs to be editable to the point that we can easily change the picture of the person and use that design for printmerlo etc. we are looking at a metalic finish business card so will need a good base colour to bring out the finish.

Target Market(s)

prospective customers

Industry/Entity Type

Business

Contact Information for Business Card

I would like one editable design that we can change the name of the card holder and profile picture. The design need to be in a format that be send to printmerlo etc.

Our address is Fenwick Lodge, Copse Lane, Ashcombe Vale, GU14 3TP Tel no. 01483 556172

Requirements
Must have
• place holder for a profile pic for the card holder. in AI or preferably PSD format

```html
<!DOCTYPE html>
<html lang="en">
<head>
<meta charset="utf-8">
<title>Veltrane Workplace Services – Business Card</title>
<link rel="stylesheet" href="https://fonts.googleapis.com/css2?family=Montserrat:wght@400;500;600;700&display=swap">
<style>
  :root {
    --stage: #e6e7ea;
    --navy: #3e5676;
    --ink: #34496a;
    --orange: #ef6a1f;
    --white: #ffffff;
    --silver: #e9ecf1;
  }
  * { box-sizing: border-box; margin: 0; padding: 0; }
  html, body { width: 1200px; height: 900px; overflow: hidden; }
  body {
    background: var(--stage);
    font-family: "Montserrat", sans-serif;
    position: relative;
  }
  .card {
    position: absolute;
    left: 280px;
    width: 640px;
    height: 366px;
    border-radius: 22px;
    overflow: hidden;
    box-shadow: 0 14px 34px rgba(20, 30, 50, 0.22);
  }
  /* Front */
  .card-front { top: 64px; background: var(--navy); }
  .portrait {
    position: absolute;
    left: 60px; bottom: 0;
    width: 300px; height: 300px;
    border-radius: 150px 150px 0 0;
    background: linear-gradient(180deg, #b98a6e 0%, #a2735c 45%, #2a2f3a 72%, #1f232b 100%);
  }
  .front-brand {
    position: absolute;
    right: 48px; top: 96px;
    text-align: right;
    color: var(--silver);
  }
  .front-brand .brand-name {
    font-weight: 700; font-size: 44px; letter-spacing: 2px; line-height: 1;
  }
  .front-brand .brand-sub {
    font-weight: 700; font-size: 16px; letter-spacing: 5.2px; margin-top: 8px;
  }
  .front-web {
    position: absolute; right: 48px; bottom: 44px;
    color: var(--white); font-size: 17px; font-weight: 500; letter-spacing: 0.5px;
  }
  .front-web b { font-weight: 700; }

  /* Back */
  .card-back { top: 478px; background: var(--white); }
  .back-brand {
    position: absolute; left: 44px; top: 196px;
    color: var(--ink);
  }
  .back-brand .brand-name {
    font-weight: 700; font-size: 40px; letter-spacing: 1.5px; line-height: 1;
  }
  .back-brand .brand-sub {
    font-weight: 700; font-size: 14.5px; letter-spacing: 4.6px; margin-top: 7px;
  }
  .divider {
    position: absolute; left: 330px; top: 58px;
    width: 2px; height: 246px;
    background: linear-gradient(180deg, var(--orange) 0%, rgba(239,106,31,0.15) 100%);
  }
  .holder {
    position: absolute; left: 356px; top: 62px; right: 30px;
  }
  .holder-name {
    color: var(--orange); font-weight: 700; font-size: 27px; letter-spacing: 1px; line-height: 1.1;
  }
  .holder-role {
    color: var(--ink); font-weight: 700; font-size: 15px; letter-spacing: 1px; margin-top: 4px;
  }
  .contact-list { list-style: none; margin-top: 18px; }
  .contact-list li {
    display: flex; align-items: center; gap: 10px;
    color: var(--ink); font-size: 15px; line-height: 25px;
  }
  .contact-list svg { width: 13px; height: 13px; flex: none; }
  .contact-list b { color: var(--orange); font-weight: 600; }
  .address {
    color: var(--ink); font-size: 15px; line-height: 23px; margin-top: 14px;
  }
</style>
</head>
<body>

  <section class="card card-front">
    <div class="portrait" role="img" aria-label="Profile photo of the card holder"></div>
    <div class="front-brand">
      <div class="brand-name">VELTRANE</div>
      <div class="brand-sub">WORKPLACE SERVICES</div>
    </div>
    <div class="front-web">www.<b>veltrane</b>.com</div>
  </section>

  <section class="card card-back">
    <div class="back-brand">
      <div class="brand-name">VELTRANE</div>
      <div class="brand-sub">WORKPLACE SERVICES</div>
    </div>

    <div class="divider"></div>

    <div class="holder">
      <div class="holder-name">MARCUS HALE</div>
      <div class="holder-role">DIRECTOR</div>

      <ul class="contact-list">
        <li>
          <svg viewBox="0 0 16 16" aria-hidden="true"><path fill="#ef6a1f" d="M3.6 1.2l2.3 2.6-1.2 1.8c.9 2 2.4 3.5 4.4 4.4l1.8-1.2 2.6 2.3-1.3 2.3C7 13.6 2.4 9 1.2 3.6z"/></svg>
          <span>01483 556172</span>
        </li>
        <li>
          <svg viewBox="0 0 16 16" aria-hidden="true"><rect x="1.5" y="3.5" width="13" height="9" rx="1" fill="none" stroke="#ef6a1f" stroke-width="1.6"/><path d="M2 4.2l6 4.6 6-4.6" fill="none" stroke="#ef6a1f" stroke-width="1.6"/></svg>
          <span>info@veltrane.com</span>
        </li>
        <li>
          <svg viewBox="0 0 16 16" aria-hidden="true"><circle cx="8" cy="8" r="6.5" fill="none" stroke="#ef6a1f" stroke-width="1.5"/><path d="M1.5 8h13M8 1.5c-3 3.5-3 9.5 0 13M8 1.5c3 3.5 3 9.5 0 13" fill="none" stroke="#ef6a1f" stroke-width="1.2"/></svg>
          <span>www.<b>veltrane</b>.com</span>
        </li>
      </ul>

      <p class="address">Fenwick Lodge, Copse Lane<br>Ashcombe Vale, GU14 3TP</p>
    </div>
  </section>

</body>
</html>
```